Communication and Marketing agency needs a new presentation card

We are a group of communication and marketing agencies specialized in companies that are in the logistics and industrial sector. The head agency is TELVANO Grupo and the group consists of 4 agencies: TELVANO Media, TELVANO Digital, TELVANO Research and DifundeEnPantalla. We hace 4 offices in Spain (Madrid, Barcelona, Valencia and Murcia). We are looking for a clean and attractive design that transmits our experience, brand presence in the market and knowledge to those who receive the card.It has to maintain the colors of the logo that is attached.
Target Market(s)
logistics and industrial sector
Marketing department
Contact Information for Business Card
Clean and attractive design

```html
<!DOCTYPE html>
<html lang="es">
<head>
<meta charset="utf-8">
<title>TELVANO Grupo – Tarjeta de presentación</title>
<link rel="stylesheet" href="https://fonts.googleapis.com/css2?family=Jost:wght@400;500;600&display=swap">
<style>
  :root {
    --brand-red: #b31b26;
    --ink: #4a4a4a;
    --ink-soft: #5c5c5c;
    --paper: #ffffff;
    --backdrop: #232323;
  }
  * { box-sizing: border-box; margin: 0; padding: 0; }
  html, body { width: 1125px; height: 1200px; overflow: hidden; }
  body {
    background: var(--backdrop);
    font-family: "Jost", "Futura", sans-serif;
    position: relative;
  }
  .card {
    position: absolute;
    left: 150px;
    width: 826px;
    height: 471px;
    overflow: hidden;
  }
  .card--front { top: 98px; background: var(--paper); }
  .card--back  { top: 631px; background: var(--brand-red); }

  /* Front */
  .wordmark {
    position: absolute;
    color: var(--brand-red);
    font-weight: 500;
    line-height: 1;
  }
  .front-wordmark { left: 46px; top: 52px; text-align: right; }
  .front-wordmark .name { display: block; font-size: 58px; letter-spacing: 2px; }
  .front-wordmark .unit { display: block; font-size: 34px; margin-top: 2px; }

  .name-band {
    position: absolute;
    left: 373px; top: 54px;
    width: 453px; height: 86px;
    background: var(--brand-red);
    color: var(--paper);
    text-align: right;
    padding: 14px 44px 0 0;
  }
  .person { font-size: 29px; font-weight: 400; line-height: 1.1; }
  .person strong { font-weight: 600; }
  .role { font-size: 21px; line-height: 1.1; opacity: .92; }

  .contact-list {
    position: absolute;
    left: 46px; top: 288px;
    list-style: none;
  }
  .contact-list li {
    display: flex; align-items: center;
    height: 27px;
    font-size: 21px;
    color: var(--ink);
  }
  .contact-list svg { width: 18px; height: 18px; margin-right: 17px; flex: none; }

  .office-list {
    position: absolute;
    right: 44px; top: 343px;
    list-style: none;
    text-align: right;
  }
  .office-list li {
    height: 27px;
    font-size: 21px;
    color: var(--ink-soft);
  }
  .office-list li::after {
    content: "";
    display: inline-block;
    width: 6px; height: 6px;
    border-radius: 50%;
    background: var(--brand-red);
    margin-left: 10px;
    vertical-align: middle;
  }

  /* Back */
  .back-wordmark {
    left: 0; right: 0; top: 128px;
    color: var(--paper);
    text-align: center;
  }
  .back-wordmark .name { display: block; font-size: 82px; letter-spacing: 3px; }
  .back-wordmark .unit { display: block; font-size: 46px; margin-top: 6px; padding-left: 250px; }

  .agency-strip {
    position: absolute;
    left: 0; top: 333px;
    width: 100%; height: 91px;
    background: var(--paper);
    display: flex;
    justify-content: space-around;
    align-items: center;
    padding: 0 14px;
  }
  .agency {
    text-align: right;
    font-weight: 500;
    line-height: 1;
  }
  .agency .name { display: block; font-size: 27px; letter-spacing: 1px; }
  .agency .unit { display: block; font-size: 18px; margin-top: 2px; }
  .agency--grey { color: var(--ink); }
  .agency--red  { color: var(--brand-red); }
  .agency--single { text-align: center; font-size: 22px; }
</style>
</head>
<body>

<section class="card card--front" aria-label="Anverso de la tarjeta">
  <div class="wordmark front-wordmark">
    <span class="name">TELVANO</span>
    <span class="unit">Media</span>
  </div>

  <div class="name-band">
    <p class="person">Lorenzo <strong>Abadía</strong></p>
    <p class="role">Director</p>
  </div>

  <ul class="contact-list">
    <li>
      <svg viewBox="0 0 18 18" aria-hidden="true"><path fill="#b31b26" d="M2 6c0-2 3-3 7-3s7 1 7 3v1h-3V5.5H5V7H2zM4 8h10l1 7H3zm5 1.5a2.3 2.3 0 1 0 0 4.6 2.3 2.3 0 0 0 0-4.6z"/></svg>
      910 555 217
    </li>
    <li>
      <svg viewBox="0 0 18 18" aria-hidden="true"><rect x="4.5" y="1" width="9" height="16" rx="1.5" fill="#b31b26"/><rect x="6" y="3" width="6" height="10" fill="#fff"/><circle cx="9" cy="15" r="1" fill="#fff"/></svg>
      600 555 418
    </li>
    <li>
      <svg viewBox="0 0 18 18" aria-hidden="true"><rect x="1" y="4" width="16" height="11" fill="#b31b26"/><path d="M1 4.5l8 6 8-6" fill="none" stroke="#fff" stroke-width="1.3"/></svg>
      labadia@telvano.es
    </li>
    <li>
      <svg viewBox="0 0 18 18" aria-hidden="true"><rect x="1.5" y="1.5" width="15" height="15" fill="#b31b26"/></svg>
      lorenzoabadia
    </li>
    <li>
      <svg viewBox="0 0 18 18" aria-hidden="true"><circle cx="9" cy="9" r="8" fill="#b31b26"/><path d="M1 9h16M9 1c-3 3-3 13 0 16M9 1c3 3 3 13 0 16" fill="none" stroke="#fff" stroke-width="1"/></svg>
      telvano.es
    </li>
  </ul>

  <ul class="office-list">
    <li>Madrid</li>
    <li>Barcelona</li>
    <li>Valencia &amp; Murcia</li>
  </ul>
</section>

<section class="card card--back" aria-label="Reverso de la tarjeta">
  <div class="wordmark back-wordmark">
    <span class="name">TELVANO</span>
    <span class="unit">Grupo</span>
  </div>

  <div class="agency-strip">
    <div class="agency agency--grey"><span class="name">TELVANO</span><span class="unit">Digital</span></div>
    <div class="agency agency--red"><span class="name">TELVANO</span><span class="unit">Media</span></div>
    <div class="agency agency--grey"><span class="name">TELVANO</span><span class="unit">Research</span></div>
    <div class="agency agency--red agency--single">DifundeEnPantalla</div>
  </div>
</section>

</body>
</html>
```